BOLD & MINIMALIST DESIGN NEEDED

We want a very bold but minimalistic business card design that is impactful and utilizes both sides of the business card. Our current logo is included for your use.

We want bold fonts and good use of negative space. We don't want the logo to overpower the design.

Target Market(s)

Professionals who are building new commercial buildings.

Industry/Entity Type

Construction

Contact Information for Business Card

Name, Title, email, office phone, cell phone, website

Font styles to use
Serif
Sans Serif

Requirements
Must have
• Bold design!

```html
<!DOCTYPE html>
<html lang="en">
<head>
<meta charset="utf-8">
<title>Ridgeline Design + Build — Business Card</title>
<link rel="stylesheet" href="https://fonts.googleapis.com/css2?family=Montserrat:wght@400;500;700;800&display=swap">
<style>
  :root {
    --page: #4a4a4a;
    --card: #1e1e1e;
    --card-shade: #262626;
    --green: #7dc243;
    --white: #ffffff;
    --muted: #d9d9d9;
    --ghost: #2e2e2e;
  }
  * { box-sizing: border-box; margin: 0; padding: 0; }
  html, body {
    width: 1200px; height: 875px; overflow: hidden;
    background: var(--page);
    font-family: "Montserrat", sans-serif;
  }
  .canvas {
    width: 1200px; height: 875px;
    display: flex; flex-direction: column; align-items: center; justify-content: center;
    gap: 44px;
  }
  .card {
    width: 660px; height: 377px;
    background: var(--card);
    border-radius: 18px;
    position: relative;
    overflow: hidden;
    box-shadow: 0 18px 40px rgba(0,0,0,.35);
  }

  /* Back side */
  .card--back { display: flex; align-items: center; justify-content: center; }
  .back-brand {
    text-align: center;
    color: var(--ghost);
    font-weight: 800;
    line-height: 1;
  }
  .back-brand__name { font-size: 58px; letter-spacing: 1px; }
  .back-brand__tag { font-size: 20px; letter-spacing: 9px; margin-top: 10px; }

  /* Front side */
  .card--front { padding: 58px 0 0 48px; }
  .front-brand { color: var(--white); font-weight: 800; line-height: 1; }
  .front-brand__name { font-size: 38px; letter-spacing: .5px; }
  .front-brand__rule { width: 250px; height: 2px; background: var(--white); margin: 6px 0 5px; }
  .front-brand__tag { font-size: 12px; letter-spacing: 6px; font-weight: 500; padding-left: 40px; }

  .person { display: flex; align-items: stretch; gap: 12px; margin-top: 34px; }
  .person__bar { width: 18px; background: var(--green); }
  .person__name { color: var(--green); font-weight: 800; font-size: 30px; line-height: 1; letter-spacing: .5px; }
  .person__title { color: var(--white); font-size: 15px; font-weight: 500; margin-top: 4px; }

  .contacts { list-style: none; margin-top: 16px; margin-left: 30px; }
  .contacts li {
    display: flex; align-items: center; gap: 9px;
    color: var(--white); font-size: 15px; font-weight: 500; line-height: 1.55;
  }
  .contacts svg { width: 13px; height: 13px; fill: var(--green); flex: none; }
  .contacts .accent { color: var(--green); }

  .front-mark {
    position: absolute; right: 40px; top: 50px;
    width: 240px; height: 240px;
    background: var(--green);
  }
</style>
</head>
<body>
<main class="canvas">

  <section class="card card--back" aria-label="Card back">
    <div class="back-brand">
      <div class="back-brand__name">RIDGELINE</div>
      <div class="back-brand__tag">DESIGN + BUILD</div>
    </div>
  </section>

  <section class="card card--front" aria-label="Card front">
    <div class="front-brand">
      <div class="front-brand__name">RIDGELINE</div>
      <div class="front-brand__rule"></div>
      <div class="front-brand__tag">DESIGN + BUILD</div>
    </div>

    <div class="person">
      <div class="person__bar"></div>
      <div>
        <div class="person__name">DORIAN VALE</div>
        <div class="person__title">Owner/CEO</div>
      </div>
    </div>

    <ul class="contacts">
      <li>
        <svg viewBox="0 0 16 16" aria-hidden="true"><path d="M3.5 1.5l2.5 0 1 3.5-1.8 1.2a8 8 0 0 0 4.6 4.6L11 9l3.5 1v2.5c0 1-1 2-2 2A11 11 0 0 1 1.5 3.5c0-1 1-2 2-2z"/></svg>
        07 5120 4400
      </li>
      <li>
        <svg viewBox="0 0 16 16" aria-hidden="true"><path d="M4.5 1h7a1 1 0 0 1 1 1v12a1 1 0 0 1-1 1h-7a1 1 0 0 1-1-1V2a1 1 0 0 1 1-1zm.5 2v9h6V3zm3 10a.8.8 0 1 0 0 1.6A.8.8 0 0 0 8 13z"/></svg>
        0412 305 761
      </li>
      <li>
        <svg viewBox="0 0 16 16" aria-hidden="true"><path d="M1 3h14v10H1zm1.5 1.3V5l5.5 4 5.5-4v-.7z"/></svg>
        hello@ridgelinebuild.com
      </li>
      <li>
        <svg viewBox="0 0 16 16" aria-hidden="true"><path d="M8 1a7 7 0 1 0 0 14A7 7 0 0 0 8 1zm0 1.5c.8 0 1.7 1.8 2 4.5H6c.3-2.7 1.2-4.5 2-4.5zM2.6 9h2.9c.1 1.7.5 3.2 1 4.3A5.5 5.5 0 0 1 2.6 9zm0-2a5.5 5.5 0 0 1 3.9-4.3c-.5 1.1-.9 2.6-1 4.3zm7.9 6.3c.5-1.1.9-2.6 1-4.3h2.9a5.5 5.5 0 0 1-3.9 4.3zM11.5 7c-.1-1.7-.5-3.2-1-4.3A5.5 5.5 0 0 1 13.4 7zM6 9h4c-.3 2.7-1.2 4.5-2 4.5S6.3 11.7 6 9z"/></svg>
        <span>www.<span class="accent">ridgelinebuild</span>.com</span>
      </li>
    </ul>

    <div class="front-mark" aria-hidden="true"></div>
  </section>

</main>
</body>
</html>
```